Website for Torvel Capital - investment banking firm

We have a corporate identity (thanks to Ravinka/31842) and want to extend that into a website design.  See the attached zipped files.
We have software folks in-house to do the coding.
See the attached Project Brief & Notes for more details.  Don't worry about the actual text - lorem ipsum will be fine.
The server will be Apache.
Thank you!
Desmond

Industry/Entity Type
Investment

```html
<!DOCTYPE html>
<html lang="en">
<head>
<meta charset="utf-8">
<title>Torvel Capital</title>
<link href="https://fonts.googleapis.com/css2?family=Open+Sans:wght@300;400;600&display=swap" rel="stylesheet">
<style>
:root{
  --brand:#1f4f9c;
  --brand-dark:#17407f;
  --nav-top:#2a63b5;
  --nav-bottom:#1b4c97;
  --ink:#333;
  --muted:#8a8a8a;
  --heading-blue:#1d4a8f;
  --footer:#245a9f;
  --footer-deep:#1c4a86;
  --footer-bar:#163e72;
  --footer-text:#e6eefa;
  --line:#dcdcdc;
}
*{margin:0;padding:0;box-sizing:border-box}
html,body{width:716px;height:1200px;overflow:hidden}
body{position:relative;background:#fff;font-family:"Open Sans",Arial,sans-serif;color:var(--ink)}
.abs{position:absolute}

.site-header{left:0;top:0;width:716px;height:78px;background:#fff}
.brand{left:43px;top:18px;display:flex;align-items:center;gap:10px}
.brand-mark{width:34px;height:34px;background:var(--brand)}
.brand-name{font-size:21px;font-weight:600;color:var(--brand);letter-spacing:.5px}

.main-nav{left:0;top:78px;width:716px;height:34px;background:linear-gradient(var(--nav-top),var(--nav-bottom))}
.main-nav a{position:absolute;top:0;line-height:34px;color:#fff;font-size:10.5px;font-weight:600;text-decoration:none;transform:translateX(-50%);white-space:nowrap}
.nav-divider{position:absolute;top:0;width:1px;height:34px;background:rgba(255,255,255,.35)}

.hero{left:0;top:112px;width:716px;height:293px;background:linear-gradient(100deg,#c9d6e4 0%,#e9eef4 35%,#d8e2ec 60%,#9aa7b4 100%)}
.hero-dots{left:334px;top:388px;display:flex;gap:3px}
.hero-dots span{width:9px;height:9px;border-radius:50%;background:#111}

.caption-band{left:0;top:405px;width:716px;height:81px;background:linear-gradient(#fff,#f2f2f2);border-top:1px solid var(--line);border-bottom:1px solid var(--line)}
.caption-title{left:55px;top:420px;font-size:19px;font-weight:400;color:#333}
.caption-sub{left:56px;top:451px;font-size:11px;font-weight:300;color:#555}
.caption-arrows{left:638px;top:440px}

.feature{width:198px}
.feature-image{width:198px;height:80px}
.feature-title{margin-top:9px;font-size:13px;font-weight:400;color:var(--heading-blue)}
.feature-text{margin-top:3px;font-size:7.6px;line-height:13.6px;color:var(--muted)}
.btn{display:block;margin-top:10px;width:64px;height:19px;background:linear-gradient(#2d5fa8,#17407f);border-radius:2px;color:#fff;font-size:7px;font-weight:600;text-align:center;line-height:19px;box-shadow:0 1px 2px rgba(0,0,0,.3)}

.col-heading{font-size:17.5px;font-weight:400;color:#333}
.col-lead{margin-top:6px;font-size:9.4px;line-height:14px;color:#555}
.col-text{margin-top:8px;font-size:7.8px;line-height:13.6px;color:var(--muted)}
.col-lead-small{margin-top:10px;font-size:7.8px;line-height:13.6px;color:#333}

.deal{display:flex;gap:8px;width:200px}
.deal-image{flex:0 0 62px;height:42px}
.deal-title{font-size:9.4px;font-weight:600;color:#444}
.deal-text{margin-top:2px;font-size:7.6px;line-height:13.4px;color:var(--muted)}

.site-footer{left:0;top:962px;width:716px;height:194px;background:radial-gradient(ellipse at 50% 30%,var(--footer) 0%,var(--footer-deep) 100%)}
.footer-col{position:absolute;top:36px}
.footer-col h3{font-size:14.5px;font-weight:400;color:#fff;margin-bottom:7px}
.footer-col li{list-style:none;font-size:8.6px;line-height:18.4px;color:var(--footer-text)}
.footer-contact li{line-height:15.3px}
.footer-bar{left:0;top:1156px;width:716px;height:44px;background:var(--footer-bar)}
.copyright{left:56px;top:17px;font-size:7.6px;color:#8fa7c9}
</style>
</head>
<body>

<header class="site-header abs">
  <div class="brand abs">
    <span class="brand-mark"></span>
    <span class="brand-name">Torvel Capital</span>
  </div>
</header>

<nav class="main-nav abs">
  <a href="#" style="left:85px">HOME</a>
  <span class="nav-divider" style="left:116px"></span>
  <a href="#" style="left:150px">ABOUT</a>
  <span class="nav-divider" style="left:184px"></span>
  <a href="#" style="left:224px">SERVICES</a>
  <span class="nav-divider" style="left:261px"></span>
  <a href="#" style="left:341px">CURRENT ENGAGEMENTS</a>
  <span class="nav-divider" style="left:418px"></span>
  <a href="#" style="left:505px">COMPLETED TRANSACTIONS</a>
  <span class="nav-divider" style="left:589px"></span>
  <a href="#" style="left:630px">CONTACT</a>
</nav>

<section class="hero abs" role="img" aria-label="Photo of a business team celebrating with a high five in a bright office"></section>
<div class="hero-dots abs"><span></span><span></span><span></span></div>

<section class="caption-band abs"></section>
<h1 class="caption-title abs">Mauris vel lacus vitae felis vestibulum volutpat</h1>
<p class="caption-sub abs">Nulla rhoncus dictum metus Curabitur tristique mi condimentum orci Phasellus pellentesque aliquam enim</p>
<svg class="caption-arrows abs" width="24" height="18" viewBox="0 0 24 18" aria-hidden="true">
  <polyline points="9,2 3,9 9,16" fill="none" stroke="#777" stroke-width="1.5"/>
  <polyline points="15,2 21,9 15,16" fill="none" stroke="#777" stroke-width="1.5"/>
</svg>

<article class="feature abs" style="left:46px;top:512px">
  <div class="feature-image" role="img" aria-label="Photo of a tablet showing financial charts on a desk" style="background:linear-gradient(120deg,#e8ecef,#c9d0d6)"></div>
  <h2 class="feature-title">FEATURS SERVICES</h2>
  <p class="feature-text">Mauris vel lacus vitae felis vestibulum volutpat Etiam est nunc venenatis in tristique eu imperdiet ac nisl Cum sociis natoque penatibus</p>
  <a class="btn" href="#">READ MORE</a>
</article>
<article class="feature abs" style="left:259px;top:512px">
  <div class="feature-image" role="img" aria-label="Illustration of business process sketches on a blue board" style="background:linear-gradient(120deg,#2b4e74,#16314f)"></div>
  <h2 class="feature-title">OUR PROCESS</h2>
  <p class="feature-text">Mauris vel lacus vitae felis vestibulum volutpat Etiam est nunc venenatis in tristique eu imperdiet ac nisl Cum sociis natoque penatibus</p>
  <a class="btn" href="#">READ MORE</a>
</article>
<article class="feature abs" style="left:472px;top:512px">
  <div class="feature-image" role="img" aria-label="Photo of a team meeting around a table" style="background:linear-gradient(120deg,#d9dde2,#a9b0b8)"></div>
  <h2 class="feature-title">OUR TEAM</h2>
  <p class="feature-text">Mauris vel lacus vitae felis vestibulum volutpat Etiam est nunc venenatis in tristique eu imperdiet ac nisl Cum sociis natoque penatibus</p>
  <a class="btn" href="#">READ MORE</a>
</article>

<section class="abs" style="left:43px;top:734px;width:196px">
  <h2 class="col-heading">About Our Company</h2>
  <p class="col-lead">Mauris vel lacus vitae felis vestibulum volut-pat Etiam est nunc venenatis</p>
  <p class="col-text">Pellentesque faucibus. Ut accumsan ultricies elit. Maecenas at justo id velit placerat molestie.</p>
  <p class="col-text" style="margin-top:7px">Donec dictum lectus non odio. Cras a ante vitae enim iaculis aliquam. Mauris nunc quam, venenatis nec, euismod sit amet, egestas placerat, est. Pellen-tesque habitant morbi tristique senectus et netus et malesuada fames ac turpis egestas. Cras id elit. Integer quis urna. Ut ante enim</p>
</section>

<section class="abs" style="left:262px;top:734px;width:196px">
  <h2 class="col-heading">Deal Structure</h2>
  <p class="col-lead-small">Successful completion of a transaction requires agreement on much more than transfer price.</p>
  <p class="col-text" style="margin-top:5px">We evaluate key factors such as the amount of consideration to be paid, timing of payments, trans-fer of obligations, co-ordination and timing of trans-fer, and details of any conditions attached to the consideration.</p>
  <p class="col-text" style="margin-top:5px">We work with clients and partners who can provide flexibility to the selling business which results in a higher probability of a transaction being concluded.</p>
</section>

<section class="abs" style="left:477px;top:729px;width:210px">
  <h2 class="col-heading">Featured Deals</h2>
  <div class="deal" style="margin-top:6px">
    <div class="deal-image" role="img" aria-label="Photo of two colleagues reviewing documents" style="background:linear-gradient(120deg,#c6ccd3,#6f7b88)"></div>
    <div><h3 class="deal-title">Praesent vitae lacus</h3><p class="deal-text">volutpat Etiam est nunc venenatis in tristique eu imperdiet ac nisl</p></div>
  </div>
  <div class="deal" style="margin-top:11px">
    <div class="deal-image" role="img" aria-label="Photo of a small business meeting" style="background:linear-gradient(120deg,#d5d8dc,#7c858e)"></div>
    <div><h3 class="deal-title">Duis non nunc</h3><p class="deal-text">volutpat Etiam est nunc venenatis in tristique eu imperdiet ac nisl Cum</p></div>
  </div>
  <div class="deal" style="margin-top:14px">
    <div class="deal-image" role="img" aria-label="Photo of a trader at computer screens" style="background:linear-gradient(120deg,#5a7fa6,#1f3550)"></div>
    <div><h3 class="deal-title">Curabitur dolordolor</h3><p class="deal-text">volutpat Etiam est nunc venenatis in tristique eu imperdiet ac nisl</p></div>
  </div>
</section>

<footer class="site-footer abs">
  <div class="footer-col" style="left:55px">
    <h3>Company</h3>
    <ul><li>Mauris vel lacus</li><li>Vitae felis</li><li>Vestibulum volutpat</li><li>Etiam est nunc</li><li>Pellentesque faucibus</li></ul>
  </div>
  <div class="footer-col" style="left:196px">
    <h3>Features</h3>
    <ul><li>Mauris vel lacus</li><li>Vitae felis</li><li>Vestibulum volutpat</li><li>Etiam est nunc</li><li>Pellentesque faucibus</li></ul>
  </div>
  <div class="footer-col" style="left:345px">
    <h3>Recent Posts</h3>
    <ul><li>Etiam est nunc venenatis tristique</li><li>Cum sociis natoque</li><li>Penatibus et magnis dis</li><li>Parturient montes nascetur</li><li>Ridiculus mus iaculis facilisis</li></ul>
  </div>
  <div class="footer-col footer-contact" style="left:514px">
    <h3>Contact Info</h3>
    <ul><li>Suite 1804 Harbourline Tower</li><li>27 - 31 Kestrel Road East</li><li>Eastbay, Hong Kong</li><li>Dallas: 1840 Marlow Parkway, Suite 410</li><li>Plano, Texas 75000</li><li>Telephone: 469-555-0147</li></ul>
  </div>
</footer>
<div class="footer-bar abs">
  <p class="copyright abs">Copyright © 2014 Company Name. All right reserved</p>
</div>

</body>
</html>
```